Process Serving Company needs a letterhead design

Looking to have a letterhead designed for letters to attorneys advertising our business. We would like something eye catching but professional. Colors and logos are attached. Please add "Process Service and Attorney Support" near the logo or header

Target Market(s)

Attorneys

Font styles to use
Serif
Sans Serif

Colors
33a6d7
0255a3
85cae6
cee9f5
ecf7fb

```html
<!DOCTYPE html>
<html lang="en">
<head>
<meta charset="utf-8">
<title>Canyon Line Serve Letterhead</title>
<link rel="stylesheet" href="https://fonts.googleapis.com/css2?family=Open+Sans:wght@400;600&display=swap">
<style>
  :root {
    --brand-blue: #0b90cd;
    --wave-grey: #bcbcbc;
    --paper: #ffffff;
    --ink: #444444;
    --ink-dark: #222222;
  }
  html, body { margin: 0; padding: 0; overflow: hidden; }
  body { width: 1040px; height: 1200px; background: var(--paper); }
  .letterhead {
    position: relative; width: 1040px; height: 1200px; overflow: hidden;
    background: var(--paper); font-family: "Open Sans", sans-serif; color: var(--ink);
  }
  .brand-name {
    position: absolute; left: 116px; top: 44px; margin: 0;
    font-size: 40px; font-weight: 400; letter-spacing: 1px;
    color: var(--brand-blue); text-transform: uppercase;
  }
  .brand-tagline {
    position: absolute; left: 113px; top: 110px; margin: 0;
    font-size: 17px; color: var(--ink-dark); letter-spacing: 0.2px;
  }
  .letter-body {
    position: absolute; left: 98px; top: 0; width: 839px;
    font-size: 15.5px; line-height: 27px;
  }
  .letter-body p { position: absolute; left: 0; width: 839px; margin: 0; text-align: justify; }
  .issue-date { top: 213px; }
  .recipient { top: 252px; line-height: 19px; }
  .salutation { top: 352px; }
  .para-1 { top: 404px; }
  .para-2 { top: 568px; }
  .para-3 { top: 676px; }
  .closing { top: 812px; }
  .signatory-name { top: 888px; font-size: 20px; font-weight: 600; color: #333; }
  .signatory-title { top: 920px; }
  .footer-wave { position: absolute; left: 0; top: 1000px; width: 1040px; height: 200px; }
  .footer-address {
    position: absolute; left: 100px; top: 1130px; margin: 0;
    font-size: 19px; line-height: 23px; color: #fff; font-style: normal;
  }
  .footer-contacts {
    position: absolute; right: 100px; top: 1088px; margin: 0; padding: 0; list-style: none;
    font-size: 19px; line-height: 23px; color: #fff; text-align: right;
  }
  .footer-contacts li { display: flex; justify-content: flex-end; align-items: center; gap: 6px; }
  .footer-contacts svg { width: 15px; height: 15px; fill: #fff; }
</style>
</head>
<body>
<main class="letterhead">
  <header>
    <h1 class="brand-name">Canyon Line Serve</h1>
    <p class="brand-tagline">PROCESS SERVICE AND ATTORNEY SUPPORT</p>
  </header>

  <section class="letter-body">
    <p class="issue-date">Issuing Date: May 5, 2018</p>
    <p class="recipient">Name Of Employee Mr. XYZABC<br>Address of Employee<br>Address Line 2 etc..</p>
    <p class="salutation">Dear Mr.XYZABC</p>
    <p class="para-1">Lorem Ipsum has been the industry's standard dummy text ever since the 1500s, when an unknown printer took a galley of type and scrambled it to make a type specimen book. It has survived not only five centuries, but also the leap into electronic typesetting, remaining essentially unchanged. It was popularised in the 1960s with the release of Transfix sheets containing Lorem Ipsum passages, and more recently with desktop publishing software like Pagewright Studio including versions of Lorem Ipsum.</p>
    <p class="para-2">Lorem Ipsum is simply dummy text of the printing and typesetting industry. Lorem Ipsum has been the industry's standard dummy text ever since the 1500s, when an unknown printer took a galley of type and scrambled it to make a type specimen book.</p>
    <p class="para-3">It has survived not only five centuries, but also the leap into electronic typesetting, remaining essentially unchanged. It was popularised in the 1960s with the release of Transfix sheets containing Lorem IpsumIpsum passages.</p>
    <p class="closing">Yours Sincerely</p>
    <p class="signatory-name">Daniel Reyes</p>
    <p class="signatory-title">Managing Director</p>
  </section>

  <footer>
    <svg class="footer-wave" viewBox="0 1000 1040 200" preserveAspectRatio="none" aria-hidden="true">
      <path d="M0 1024 C150 1108 380 1118 650 1062 L1040 1062 L1040 1200 L0 1200 Z" fill="var(--wave-grey)"/>
      <path d="M0 1072 C180 1128 390 1124 620 1080 C800 1046 950 1040 1040 1045 L1040 1200 L0 1200 Z" fill="var(--brand-blue)" stroke="#fff" stroke-width="4"/>
    </svg>
    <address class="footer-address">4120 E Mesa Ridge Rd #210<br>Sunvale AZ 85099</address>
    <ul class="footer-contacts">
      <li>555-201-4470 <svg viewBox="0 0 16 16"><path d="M2 6c0-2 2-3 6-3s6 1 6 3v1h-3V5.5H5V7H2zM4 8h8l2 6H2z"/></svg></li>
      <li>555-201-4471 <svg viewBox="0 0 16 16"><path d="M4 1h8v4H4zM1 6h14v6h-3v3H4v-3H1zM5 10v4h6v-4z"/></svg></li>
      <li>info@canyonlineserve.com <svg viewBox="0 0 16 16"><path d="M1 3h14v10H1zM2 4.5v.5l6 4 6-4v-.5z"/></svg></li>
      <li>www.canyonlineserve.com <svg viewBox="0 0 16 16"><circle cx="8" cy="8" r="7"/></svg></li>
    </ul>
  </footer>
</main>
</body>
</html>
```